The Brookhaven Sessions - Concert Series Website Design

I've recently decided to launch a concert series in my living room and would love a website to use to promote the series. I'm looking for a simple Wix design that I could take over once it's complete. I'll provide the logo for which I'd like the website to utilize the color scheme.

Target Market(s)

Music lovers in Denver

Industry/Entity Type

Music

Coding

Coded - Design and coding required

Number of Pages Required

2 page

Font styles to use
Script

Requirements
Must have
• 2 pages - one for concert goers to see the schedule and rsvp, and one for artists about the booking process

```html
<!DOCTYPE html>
<html lang="en">
<head>
<meta charset="utf-8">
<title>The Brookhaven Sessions</title>
<link href="https://fonts.googleapis.com/css2?family=Outfit:wght@300;400;500;600;700&display=swap" rel="stylesheet">
<style>
:root{
  --cream:#fdf1a9;
  --cream-soft:#fbeec0;
  --maroon:#6e1a2a;
  --maroon-deep:#4a1022;
  --wine:#7a1f2b;
  --plum:#3a1350;
  --plum-deep:#2a0c3c;
  --white:#ffffff;
  --text-dark:#5b1420;
}
*{box-sizing:border-box;margin:0;padding:0}
html,body{width:1200px;height:3155px;overflow:hidden}
body{font-family:"Outfit",sans-serif;background:var(--maroon);color:var(--white);position:relative}
.abs{position:absolute}

/* header */
.site-header{position:absolute;left:0;top:0;width:1200px;height:102px;background:var(--white)}
.brand{position:absolute;left:144px;top:22px;display:flex;align-items:center;gap:14px}
.brand-mark{width:58px;height:58px;border-radius:50%;background:var(--maroon)}
.brand-name{font-size:24px;font-weight:500;color:var(--maroon);line-height:1.05;width:170px}
.nav{position:absolute;right:142px;top:38px;display:flex;gap:40px}
.nav a{font-size:19px;font-weight:500;color:var(--maroon);text-decoration:none;position:relative}
.nav a.active::before{content:"";position:absolute;left:0;top:-16px;width:53px;height:4px;border-radius:2px;background:var(--maroon)}

/* hero */
.hero{position:absolute;left:0;top:102px;width:1200px;height:619px;
  background:radial-gradient(circle at 880px 260px,#8a5a3a 0%,#4a2a2a 30%,transparent 55%),
  radial-gradient(circle at 680px 180px,#6a3a2a 0%,transparent 30%),
  linear-gradient(90deg,#3a1a20 0%,#2a1018 45%,#3a2020 100%)}
.hero-title{position:absolute;left:142px;top:148px;font-size:64px;font-weight:700;line-height:63px;color:var(--cream)}
.hero-sub{position:absolute;left:144px;top:366px;font-size:19px;font-weight:600}
.btn{display:inline-flex;align-items:center;justify-content:center;background:var(--cream);color:var(--text-dark);font-weight:600;border-radius:4px}
.hero .btn{position:absolute;left:144px;top:411px;width:126px;height:50px;font-size:17px}

/* rsvp */
.rsvp{position:absolute;left:0;top:721px;width:1200px;height:722px;
  background:linear-gradient(180deg,#6e1a2a 0%,#7c1f28 60%,#8a2a24 100%)}
.rsvp-ridge{position:absolute;left:0;bottom:0;width:1200px;height:60px}
.section-title{font-size:50px;font-weight:700;color:var(--cream)}
.rsvp .section-title{position:absolute;left:142px;top:120px}
.label{position:absolute;font-size:24px;font-weight:600}
.field{position:absolute;height:73px;border:2px solid var(--white);border-radius:14px}
.hint{position:absolute;font-size:17px}
.rsvp .btn{position:absolute;left:144px;top:538px;width:184px;height:64px;font-size:22px}
.note{position:absolute;left:355px;top:561px;font-size:16px;font-style:italic}

/* about */
.about{position:absolute;left:0;top:1443px;width:1200px;height:461px;
  background:linear-gradient(90deg,#2a0c3c 0%,#3a1350 50%,#5a1a4a 100%)}
.about-photo{position:absolute;left:673px;top:0;width:527px;height:461px;
  background:radial-gradient(circle at 270px 200px,#e0a8a0 0%,#9a4a7a 35%,#4a1650 75%,transparent 100%)}
.about .section-title{position:absolute;left:142px;top:122px;font-size:50px}
.about-sub{position:absolute;left:142px;top:183px;font-size:29px;font-weight:600;line-height:36px;color:var(--cream)}
.about-text{position:absolute;left:144px;top:266px;width:560px;font-size:20px;font-weight:300;line-height:28px}

/* sessions */
.sessions{position:absolute;left:0;top:1904px;width:1200px;height:946px;
  background:linear-gradient(180deg,#6a1a2e 0%,#5a1a3c 50%,#3e1242 100%)}
.sessions .section-title{position:absolute;left:142px;top:108px}
.arrow{position:absolute;top:123px;width:46px;height:46px;border-radius:50%;background:var(--white)}
.arrow svg{position:absolute;left:15px;top:15px}
.card{position:absolute;left:143px;width:914px;height:169px;border:2px solid var(--white);border-radius:30px;background:rgba(255,255,255,.16)}
.card-date{position:absolute;left:52px;top:28px;font-size:50px;font-weight:600;line-height:60px}
.card-place{position:absolute;font-size:20px;font-weight:300;top:102px}
.card-divider{position:absolute;left:260px;top:30px;width:2px;height:108px;background:rgba(255,255,255,.6)}
.card-act{position:absolute;left:308px;top:34px;font-size:43px;font-weight:300;line-height:52px}
.card .btn{position:absolute;left:734px;top:40px;width:126px;height:50px;font-size:17px;box-shadow:0 4px 10px rgba(0,0,0,.3)}
.card .btn.active{background:var(--maroon-deep);color:var(--white)}

/* footer */
.site-footer{position:absolute;left:0;top:2850px;width:1200px;height:305px;
  background:radial-gradient(ellipse at 600px 320px,#c05a3a 0%,#7a2a3a 35%,transparent 70%),
  linear-gradient(180deg,#2e0c30 0%,#4a1438 60%,#6a2030 100%)}
.follow{position:absolute;left:0;width:1200px;top:90px;text-align:center;font-size:20px;font-weight:600;color:var(--cream)}
.social{position:absolute;top:138px;width:56px;height:56px;border-radius:50%;background:var(--cream)}
.social svg{position:absolute;left:18px;top:19px}
.copyright{position:absolute;left:0;width:1200px;top:232px;text-align:center;font-size:21px;font-weight:300;color:var(--cream)}
</style>
</head>
<body>

<header class="site-header">
  <div class="brand">
    <div class="brand-mark"></div>
    <div class="brand-name">The Brookhaven Sessions</div>
  </div>
  <nav class="nav">
    <a href="#" class="active">Concerts</a>
    <a href="#">For Artists</a>
  </nav>
</header>

<section class="hero" role="img" aria-label="Photo of a singer with guitar performing in a warmly lit room with band behind">
  <h1 class="hero-title">Live Music.<br>Shared Space.<br>Golden-hour Energy.</h1>
  <p class="hero-sub">An intimate living-room concert series in Denver.</p>
  <a class="btn">Join Us</a>
</section>

<section class="rsvp">
  <h2 class="section-title">We Look Forward to Your Response.</h2>
  <div class="label" style="left:142px;top:206px">Name</div>
  <div class="field" style="left:142px;top:255px;width:446px"></div>
  <div class="field" style="left:611px;top:255px;width:446px"></div>
  <div class="hint" style="left:142px;top:343px">First name</div>
  <div class="hint" style="left:611px;top:343px">Last name</div>
  <div class="label" style="left:142px;top:387px">Email</div>
  <div class="label" style="left:611px;top:387px">Number of guests</div>
  <div class="field" style="left:142px;top:436px;width:446px"></div>
  <div class="field" style="left:611px;top:436px;width:446px"></div>
  <a class="btn">Submit Now</a>
  <p class="note">Exact address and details sent via email after RSVP.</p>
  <svg class="rsvp-ridge" viewBox="0 0 1200 60" preserveAspectRatio="none">
    <path d="M0 40 Q150 15 300 30 T600 25 T900 35 T1200 28 V60 H0Z" fill="#9a3226" opacity=".6"/>
  </svg>
</section>

<section class="about">
  <div class="about-photo" role="img" aria-label="Photo of a guitarist in a cap singing into a microphone"></div>
  <h2 class="section-title">About the Series</h2>
  <p class="about-sub">Be a Performer at<br>The Brookhaven Sessions</p>
  <p class="about-text">The Brookhaven Sessions is a small, invitation-style concert series hosted in a Denver living room—created to bring artists and listeners closer, one performance at a time.</p>
</section>

<section class="sessions">
  <h2 class="section-title">Upcoming Sessions</h2>
  <div class="arrow" style="left:927px"><svg width="16" height="16" viewBox="0 0 16 16"><path d="M10 3 L5 8 L10 13" stroke="#222" stroke-width="2" fill="none"/></svg></div>
  <div class="arrow" style="left:983px"><svg width="16" height="16" viewBox="0 0 16 16"><path d="M6 3 L11 8 L6 13" stroke="#222" stroke-width="2" fill="none"/></svg></div>

  <article class="card" style="top:222px">
    <div class="card-date">May 10</div>
    <div class="card-place" style="left:52px">Denver,Paatt</div>
    <div class="card-divider"></div>
    <div class="card-act">John Doe Band</div>
    <div class="card-place" style="left:308px">Denver,Paatt 25</div>
    <a class="btn active">Join Us</a>
  </article>
  <article class="card" style="top:421px">
    <div class="card-date">May 24</div>
    <div class="card-place" style="left:52px">Denver,Paatt</div>
    <div class="card-divider"></div>
    <div class="card-act">Jane Smith Trio</div>
    <div class="card-place" style="left:308px">Denver,Paatt 25</div>
    <a class="btn">Join Us</a>
  </article>
  <article class="card" style="top:621px">
    <div class="card-date">June 07</div>
    <div class="card-place" style="left:52px">Denver,Paatt</div>
    <div class="card-divider"></div>
    <div class="card-act">The Folk Collective</div>
    <div class="card-place" style="left:308px">Denver,Paatt 25</div>
    <a class="btn">Join Us</a>
  </article>
</section>

<footer class="site-footer">
  <p class="follow">Follow Us:</p>
  <div class="social" style="left:540px"><svg width="20" height="16" viewBox="0 0 20 16"><rect x="0" y="0" width="20" height="16" rx="2" fill="#5b1420"/><path d="M1 2 L10 9 L19 2" stroke="#fdf1a9" stroke-width="1.6" fill="none"/></svg></div>
  <div class="social" style="left:604px"></div>
  <p class="copyright">© Copyrights 2026 The Brookhaven Sessions | All Rights Reserved</p>
</footer>

</body>
</html>
```